The most modern business card ever !!!

Our company call “Vendalo”. Vendalo is a technology company specialized in cruises solutions. Out main product is a platform to reserve cruises. This is a revolutionary platform that make easier to travel agencies and final users to reserve cruises across dozen companies like tibba, wernu, hpv, dgb, etc..We are a “start up”, with a young team of developers and we want to transmit it.. For it, we want something different, a modern business card that represent cruises and technology.. When someone receive this card, this person should say: wowww this is different… this is modern… this is a cruise related company..
- diferent, modern
- traditions business card

```html
<!DOCTYPE html>
<html lang="en">
<head>
<meta charset="utf-8">
<title>Vendalo business card</title>
<link href="https://fonts.googleapis.com/css2?family=Open+Sans:wght@400;600;700&display=swap" rel="stylesheet">
<style>
  :root {
    --stage: #1c1c1e;
    --card: #141416;
    --card-edge: #262628;
    --band: rgba(255,255,255,0.035);
    --ink: #ffffff;
    --muted: #c9c9cc;
    --accent: #1fa3e0;
    --rule: #3a3a3d;
  }
  * { box-sizing: border-box; margin: 0; padding: 0; }
  html, body { width: 1200px; height: 900px; overflow: hidden; }
  body {
    background: var(--stage);
    font-family: "Open Sans", Arial, sans-serif;
    display: flex; flex-direction: column; align-items: center; justify-content: center;
    gap: 50px;
  }
  .card {
    position: relative;
    width: 595px; height: 340px;
    background: var(--card);
    border: 1px solid var(--card-edge);
    border-radius: 26px;
    overflow: hidden;
  }
  .card__band {
    position: absolute; top: 0; left: 60px;
    width: 90px; height: 100%;
    background: var(--band);
  }
  .wordmark {
    font-weight: 600; color: var(--ink);
    letter-spacing: 1px; line-height: 1;
  }
  /* front */
  .card--front .wordmark {
    position: absolute; left: 0; right: 0; top: 130px;
    text-align: center; font-size: 62px;
  }
  .card--front .website {
    position: absolute; right: 150px; bottom: 46px;
    font-size: 14px; color: var(--muted);
  }
  /* back */
  .card--back .wordmark {
    position: absolute; right: 70px; top: 60px; font-size: 62px;
  }
  .card--back .divider {
    position: absolute; left: 250px; right: 40px; top: 160px;
    height: 1px; background: var(--rule);
  }
  .person { position: absolute; left: 48px; top: 180px; }
  .person__name {
    color: var(--accent); font-weight: 700; font-size: 20px;
    letter-spacing: 0.5px; text-transform: uppercase;
  }
  .person__role { color: var(--muted); font-size: 16px; margin-top: -2px; }
  .contacts { list-style: none; margin-top: 16px; }
  .contacts li {
    display: flex; align-items: center; gap: 8px;
    color: var(--muted); font-size: 17px; line-height: 24px;
  }
  .contacts svg { width: 14px; height: 14px; fill: var(--accent); flex: none; }
  .address {
    position: absolute; right: 36px; top: 180px;
    text-align: right; color: var(--muted); font-size: 16px; line-height: 22px;
  }
</style>
</head>
<body>
  <section class="card card--front" aria-label="Card front">
    <div class="card__band"></div>
    <div class="wordmark">Vendalo</div>
    <div class="website">www.vendalo.io</div>
  </section>

  <section class="card card--back" aria-label="Card back">
    <div class="card__band"></div>
    <div class="wordmark">Vendalo</div>
    <div class="divider"></div>
    <div class="person">
      <div class="person__name">Marek Olsen</div>
      <div class="person__role">Managing Director</div>
      <ul class="contacts">
        <li><svg viewBox="0 0 16 16" aria-hidden="true"><path d="M2 3c0-1 1-2 2-2h2l1 4-2 1c1 2 3 4 5 5l1-2 4 1v2c0 1-1 2-2 2C7 15 1 9 2 3z"/></svg>044-555 210 873</li>
        <li><svg viewBox="0 0 16 16" aria-hidden="true"><path d="M4 0h8a1 1 0 0 1 1 1v14a1 1 0 0 1-1 1H4a1 1 0 0 1-1-1V1a1 1 0 0 1 1-1zm1 2v10h6V2zm3 11a1 1 0 1 0 0 2 1 1 0 0 0 0-2z"/></svg>044-555 210 873</li>
        <li><svg viewBox="0 0 16 16" aria-hidden="true"><path d="M0 3h16v10H0zm1 1v.5l7 5 7-5V4z"/></svg>info@vendalo.io</li>
      </ul>
    </div>
    <div class="address">48 Harbour Lane, Suite 7<br>Portside City, 480210</div>
  </section>
</body>
</html>
```